Corporate Business Card

Very professional, Modern, Not to busy, include phone address email, website
(253) 617-4930, 18761 52nd Avenue S, Brookvale, OR 98047, martin@plumlinegroup.com, varkoworks.com

Target Market(s)

Manufacturing

Industry/Entity Type

Aero, machining, manufacturing, Off road racing

Contact Information for Business Card

Phone, address email, website

```html
<!DOCTYPE html>
<html lang="en">
<head>
<meta charset="utf-8">
<title>Varko Works – Business Card</title>
<link rel="stylesheet" href="https://fonts.googleapis.com/css2?family=Exo+2:wght@400;500;700&display=swap">
<style>
  :root {
    --stage: #2a2a2a;
    --navy: #17366e;
    --navy-deep: #0f2450;
    --white: #ffffff;
    --red: #d3212c;
    --card-w: 600px;
    --card-h: 343px;
  }
  * { box-sizing: border-box; margin: 0; padding: 0; }
  html, body { width: 1200px; height: 1015px; overflow: hidden; }
  body {
    background: var(--stage);
    font-family: "Exo 2", sans-serif;
    display: flex;
    flex-direction: column;
    align-items: center;
    justify-content: center;
    gap: 64px;
  }
  .card {
    position: relative;
    width: var(--card-w);
    height: var(--card-h);
    background: var(--navy);
    overflow: hidden;
    box-shadow: 0 14px 30px rgba(0,0,0,.45);
  }
  /* back side */
  .card-back { display: flex; align-items: center; justify-content: center; padding-bottom: 30px; }
  .card-back .brand-name {
    font-size: 54px;
    font-weight: 700;
    color: var(--navy-deep);
    letter-spacing: 2px;
    text-transform: uppercase;
    white-space: nowrap;
  }
  /* front side */
  .front-art { position: absolute; inset: 0; }
  .front-brand {
    position: absolute;
    left: 350px;
    top: 145px;
    width: 230px;
    text-align: center;
    font-size: 30px;
    font-weight: 700;
    color: var(--navy);
    text-transform: uppercase;
    letter-spacing: 1px;
    white-space: nowrap;
  }
  .contact-list {
    position: absolute;
    left: 40px;
    list-style: none;
    color: var(--white);
    font-size: 15px;
    font-weight: 500;
    line-height: 1.5;
    white-space: nowrap;
  }
  .contact-list.top { top: 40px; }
  .contact-list.bottom { bottom: 40px; }
  .contact-list li { display: flex; align-items: flex-start; gap: 10px; }
  .contact-list svg { width: 14px; height: 14px; flex: none; margin-top: 4px; fill: var(--red); }
</style>
</head>
<body>

  <section class="card card-back" aria-label="Card back">
    <span class="brand-name">Varko Works</span>
  </section>

  <section class="card card-front" aria-label="Card front">
    <svg class="front-art" viewBox="0 0 600 343" aria-hidden="true">
      <path d="M600 0 H330 A235 235 0 0 0 460 343 H600 Z" fill="#ffffff"/>
      <path d="M355 25 A215 215 0 0 0 500 318" fill="none" stroke="#d3212c" stroke-width="3"/>
    </svg>

    <div class="front-brand">Varko Works</div>

    <ul class="contact-list top">
      <li>
        <svg viewBox="0 0 24 24"><path d="M6.6 10.8a15 15 0 0 0 6.6 6.6l2.2-2.2c.3-.3.7-.4 1-.2 1.1.4 2.3.6 3.6.6.6 0 1 .4 1 1V20c0 .6-.4 1-1 1A17 17 0 0 1 3 4c0-.6.4-1 1-1h3.5c.6 0 1 .4 1 1 0 1.3.2 2.5.6 3.6.1.3 0 .7-.2 1z"/></svg>
        (555) 617-4930
      </li>
      <li>
        <svg viewBox="0 0 24 24"><path d="M2 5h20v14H2z M2 5l10 8 10-8" stroke="#17366e" stroke-width="1.5"/></svg>
        martin@plumlinegroup.com
      </li>
      <li>
        <svg viewBox="0 0 24 24"><path d="M12 2a10 10 0 1 0 0 20 10 10 0 0 0 0-20zm0 2c1 1.2 1.8 3.3 2 6h-4c.2-2.7 1-4.8 2-6zM4.1 10c.4-2.7 2.2-4.9 4.6-5.8-.8 1.6-1.4 3.6-1.6 5.8zm0 4h3c.2 2.2.8 4.2 1.6 5.8A8 8 0 0 1 4.1 14zm5.9 0h4c-.2 2.7-1 4.8-2 6-1-1.2-1.8-3.3-2-6zm6.9 0h3a8 8 0 0 1-4.6 5.8c.8-1.6 1.4-3.6 1.6-5.8zm0-4c-.2-2.2-.8-4.2-1.6-5.8A8 8 0 0 1 19.9 10z"/></svg>
        www.varkoworks.com
      </li>
    </ul>

    <ul class="contact-list bottom">
      <li>
        <svg viewBox="0 0 24 24"><path d="M12 2a7 7 0 0 0-7 7c0 5 7 13 7 13s7-8 7-13a7 7 0 0 0-7-7zm0 9.5A2.5 2.5 0 1 1 12 6.5a2.5 2.5 0 0 1 0 5z"/></svg>
        <span>18761 52nd Avenue S<br>Brookvale, OR 98047</span>
      </li>
    </ul>
  </section>

</body>
</html>
```